Logo, Web and Mobile Designs for enterprise social media platform

All the details are in the attached document, please start reading the scope document first which explains what is this project about and the details about the needed deliverables, after that please read the UI_Requirements document which will detail what is expected regarding the coded web version since this is a coded contest, it is very important that you meet the UI requirements or suggest something else but we will need to agree first before working on the coded version

Good Luck

Target Market(s)

Enterprise Social Media

Industry/Entity Type

Media

Coding

Coded - Design and coding required

Number of Pages Required

5+ page

Font styles to use
Sans Serif

Requirements
Must have
• All the must haves are listed in the scope document so please check before you start

```html
<!DOCTYPE html>
<html lang="en">
<head>
<meta charset="utf-8">
<title>Teamora – News Feed</title>
<link rel="stylesheet" href="https://fonts.googleapis.com/css2?family=Roboto:wght@300;400;500;700;900&display=swap">
<style>
:root{
  --bar:#3f3f3f;
  --bar-field:#5a5a5a;
  --page:#f1f1f1;
  --card:#ffffff;
  --line:#e6e6e6;
  --text:#333333;
  --muted:#8c8c8c;
  --soft:#b4b4b4;
  --accent:#f0541e;
  --online:#1fae3f;
  --panel:#d9d9d9;
  --ad-fill-top:#e9edf3;
  --ad-fill-bottom:#6f94c9;
}
*{box-sizing:border-box;margin:0;padding:0}
html,body{width:754px;height:1200px;overflow:hidden}
body{position:relative;background:var(--page);font-family:'Roboto',sans-serif;color:var(--text);font-size:8px}
.abs{position:absolute}

/* top bar */
.topbar{left:0;top:0;width:754px;height:38px;background:var(--bar);box-shadow:0 1px 3px rgba(0,0,0,.3)}
.brand{left:62px;top:8px;color:#fff;font-size:17px;font-weight:300;letter-spacing:.2px}
.search{left:154px;top:8px;width:173px;height:21px;background:var(--bar-field);color:#bdbdbd;font-size:6.5px;padding:7px 8px;letter-spacing:.3px}
.search svg{position:absolute;right:7px;top:6px}
.nav{top:0;height:38px;display:flex;align-items:center;color:#d5d5d5;font-size:7.5px}
.nav-sep{top:0;width:1px;height:38px;background:#555}
.avatar-top{left:595px;top:5px;width:28px;height:28px;border-radius:50%;background:linear-gradient(#9aa7b2,#5e6a74);border:2px solid #cfd6dc}
.user{left:627px;top:14px;color:#fff;font-size:7.5px;font-weight:500}

/* left menu */
.menu{left:61px;top:54px;width:121px;background:var(--card)}
.menu li{list-style:none;height:27px;border-bottom:1px solid var(--line);display:flex;align-items:center;padding-left:12px;font-size:7.3px;color:#444}
.menu li:last-child{border-bottom:0}
.menu li i{width:7px;height:6px;background:#9a9a9a;margin-right:11px;border-radius:1px}
.block-head{background:var(--bar);color:#fff;font-weight:700;font-size:8px;letter-spacing:1.6px;padding:0 9px;height:23px;display:flex;align-items:center}
.subscribe{left:61px;top:478px;width:121px}
.subscribe .body{background:var(--card);padding:12px 10px 11px;height:107px}
.field{border:1px solid #d8d8d8;height:23px;font-size:6.5px;color:#555;padding:8px 9px;margin-bottom:4px}
.btn-sub{background:var(--accent);color:#fff;font-weight:700;font-size:7.8px;letter-spacing:1.5px;height:25px;display:flex;align-items:center;justify-content:center;margin-top:6px}

/* ad slot */
.ad-frame{left:61px;top:620px;width:121px;height:356px;background:var(--panel)}
.ad{position:absolute;left:17px;top:16px;width:86px;height:322px;border:1px solid #555;background:linear-gradient(var(--ad-fill-top),var(--ad-fill-bottom))}

/* composer */
.composer{left:190px;top:54px;width:360px;height:115px;background:#e4e4e4}
.composer .box{position:absolute;left:13px;top:11px;width:334px;height:55px;background:#fff;border:1px solid #d4d4d4;padding:11px 10px;font-size:7.5px;color:#333}
.composer .box:after{content:"";position:absolute;left:16px;bottom:-7px;border:6px solid transparent;border-top-color:#fff;border-bottom:0}
.tools{position:absolute;left:13px;top:78px;width:334px;display:flex;justify-content:space-around}
.tool{display:flex;flex-direction:column;align-items:center;font-size:6.8px;color:#a5a5a5;width:40px}
.tool svg{margin-bottom:3px}
.tool.on{color:#333}

/* posts */
.post{left:190px;width:360px;background:var(--card)}
.post .head{position:absolute;left:9px;top:9px;display:flex}
.post .pic{width:28px;height:28px;background:linear-gradient(#7a8590,#3e4650);margin-right:8px}
.post .name{font-size:7.5px;color:#222;margin-top:2px}
.post .time{font-size:6px;color:var(--soft);margin-top:3px}
.post .photo{position:absolute;left:9px;top:45px;width:340px}
.actions{position:absolute;left:9px;display:flex;font-size:7.5px;color:#777}
.actions span{display:flex;align-items:center;margin-right:20px}
.actions svg{margin-right:4px}
.reply{left:190px;width:360px;height:26px;display:flex;align-items:center}
.reply .me{width:19px;height:19px;background:linear-gradient(#9fb0bd,#5b6770);margin:0 14px 0 11px}
.reply .input{flex:0 0 301px;height:20px;background:#fff;border:1px solid #d7d7d7;font-size:6px;color:#aaa;padding:6px 7px;position:relative}
.reply .input svg{position:absolute;right:7px;top:6px}

/* right column */
.people{left:559px;top:54px;width:133px;background:var(--card)}
.person{height:32.5px;margin:0 8px;border-bottom:1px solid var(--line);display:flex;align-items:center;font-size:7.3px;color:#555}
.person:last-child{border-bottom:0}
.person b{width:25px;height:25px;background:linear-gradient(#8f9aa4,#4d5760);margin:0 6px 0 1px}
.person i{margin-left:auto;width:4px;height:4px;border-radius:50%;background:var(--online);margin-right:6px}
.people-search{left:559px;top:330px;width:133px;height:40px;background:var(--panel);display:flex;align-items:center;padding-left:13px;font-size:7.5px;color:#444}
.people-search svg{margin-right:9px}
.events{left:559px;top:383px;width:133px}
.events ul{background:var(--card);padding:5px 5px 8px 8px}
.events li{list-style:none;border-bottom:1px solid var(--line);font-size:7.2px;line-height:11.5px;color:#555;padding:8px 16px 5px 15px;position:relative}
.events li:last-child{border-bottom:0;padding-right:4px}
.events li:before{content:"»";position:absolute;left:1px;top:7px;color:#777}
.about{left:559px;top:694px;width:133px}
.about .body{background:var(--card);padding:14px 20px 15px 16px;font-size:7.2px;line-height:11.8px;color:#555}
.about .more{color:var(--accent);font-weight:700;letter-spacing:1px;font-size:7px;margin-top:13px}

.footer{left:0;top:1162px;width:754px;height:38px;background:var(--bar);color:#d8d8d8;font-size:6.8px;display:flex;align-items:center;justify-content:center}
</style>
</head>
<body>

<header class="abs topbar"></header>
<div class="abs brand">Teamora</div>
<div class="abs search">SEARCH
  <svg width="8" height="8" viewBox="0 0 8 8"><circle cx="3.3" cy="3.3" r="2.5" fill="none" stroke="#ccc" stroke-width="1.1"/><path d="M5.2 5.2L7.5 7.5" stroke="#ccc" stroke-width="1.1"/></svg>
</div>
<div class="abs nav-sep" style="left:420px"></div>
<div class="abs nav" style="left:438px">Home</div>
<div class="abs nav-sep" style="left:476px"></div>
<div class="abs nav" style="left:489px">My Profile</div>
<div class="abs nav-sep" style="left:536px"></div>
<div class="abs nav" style="left:553px">Blog</div>
<div class="abs nav-sep" style="left:583px"></div>
<div class="abs avatar-top" role="img" aria-label="Profile photo of the signed-in user"></div>
<div class="abs user">Daniel Moreau</div>

<ul class="abs menu">
  <li><i></i>Edit Profile</li><li><i></i>Messages</li><li><i></i>Games</li><li><i></i>Events</li>
  <li><i></i>New Groups</li><li><i></i>Create Group</li><li><i></i>Office Friends</li><li><i></i>News Feeds</li>
  <li><i></i>Photos</li><li><i></i>Videos</li><li><i></i>Pages</li><li><i></i>Status</li>
  <li><i></i>Blog</li><li><i></i>Contact Us</li><li><i></i>Create Event</li>
</ul>

<section class="abs subscribe">
  <div class="block-head">SUBSCRIBE</div>
  <div class="body">
    <div class="field">Name</div>
    <div class="field">E mail</div>
    <div class="btn-sub">SUBSCRIBE!</div>
  </div>
</section>

<aside class="abs ad-frame">
  <div class="ad" role="img" aria-label="Vertical advertising banner for an internet access provider"></div>
</aside>

<section class="abs composer">
  <div class="box">Share What's New...</div>
  <div class="tools">
    <div class="tool on"><svg width="13" height="13" viewBox="0 0 13 13"><path d="M2 11l1-3 6-6 2 2-6 6z" fill="#f0541e"/></svg>Text</div>
    <div class="tool"><svg width="13" height="13" viewBox="0 0 13 13"><rect x="1" y="3.5" width="11" height="8" rx="1" fill="#aaa"/><rect x="4.5" y="2" width="4" height="2" fill="#aaa"/><circle cx="6.5" cy="7.5" r="2.3" fill="#fff"/></svg>Photos</div>
    <div class="tool"><svg width="13" height="13" viewBox="0 0 13 13"><rect x="1" y="2.5" width="11" height="8" rx="1.5" fill="#aaa"/><path d="M5 4.5l3.5 2-3.5 2z" fill="#fff"/></svg>Videos</div>
    <div class="tool"><svg width="13" height="13" viewBox="0 0 13 13"><rect x="1.5" y="1.5" width="5" height="3.5" rx="1.7" transform="rotate(45 4 3.2)" fill="none" stroke="#aaa" stroke-width="1.2"/><rect x="6.5" y="7.5" width="5" height="3.5" rx="1.7" transform="rotate(45 9 9.2)" fill="none" stroke="#aaa" stroke-width="1.2"/></svg>Links</div>
    <div class="tool"><svg width="13" height="13" viewBox="0 0 13 13"><rect x="1.5" y="2.5" width="10" height="9" fill="none" stroke="#aaa" stroke-width="1.2"/><path d="M1.5 5h10M4 1v3M9 1v3" stroke="#aaa" stroke-width="1.2"/></svg>Event</div>
    <div class="tool"><svg width="13" height="13" viewBox="0 0 13 13"><path d="M1 12h11" stroke="#aaa"/><rect x="2" y="6" width="1.6" height="5" fill="#aaa"/><rect x="5" y="3" width="1.6" height="8" fill="#aaa"/><rect x="8" y="5" width="1.6" height="6" fill="#aaa"/><rect x="10.5" y="2" width="1.2" height="9" fill="#aaa"/></svg>Poll</div>
  </div>
</section>

<!-- post 1 -->
<article class="abs post" style="top:169px;height:219px">
  <div class="head"><div class="pic" role="img" aria-label="Author photo"></div><div><div class="name">Victor Hallam</div><div class="time">10 hrs</div></div></div>
  <div class="photo" style="height:145px;background:linear-gradient(100deg,#4b4a55 0%,#8a8a96 45%,#b8bfcc 70%,#e6e9ee 100%)" role="img" aria-label="Businessman on a phone call by a window over an industrial skyline"></div>
  <div class="actions" style="top:200px"><span><svg width="8" height="7"><rect width="2" height="6" y="1" fill="#aaa"/><path d="M3 1h4v6H3z" fill="#aaa"/></svg>Like</span><span><svg width="9" height="7"><ellipse cx="4.5" cy="3" rx="4.5" ry="3" fill="#aaa"/></svg>Comment</span><span><svg width="8" height="7"><circle cx="1.5" cy="3.5" r="1.3" fill="#aaa"/><circle cx="6.5" cy="1.3" r="1.3" fill="#aaa"/><circle cx="6.5" cy="5.7" r="1.3" fill="#aaa"/><path d="M1.5 3.5L6.5 1.3M1.5 3.5L6.5 5.7" stroke="#aaa"/></svg>Share</span></div>
</article>
<div class="abs reply" style="top:393px"><div class="me" role="img" aria-label="Your photo"></div><div class="input">Write Comment...<svg width="8" height="7"><rect y="1.5" width="8" height="5.5" rx="1" fill="#999"/><circle cx="4" cy="4.2" r="1.5" fill="#fff"/></svg></div></div>

<!-- post 2 -->
<article class="abs post" style="top:424px;height:220px">
  <div class="head"><div class="pic" role="img" aria-label="Author photo"></div><div><div class="name">Mark</div><div class="time">10 hrs</div></div></div>
  <div class="photo" style="height:145px;background:linear-gradient(120deg,#7a5a3c 0%,#a98a66 35%,#3c3c3c 55%,#8d6e4e 80%,#c9b69a 100%)" role="img" aria-label="Laptop, coffee and plant on a wooden desk"></div>
  <div class="actions" style="top:202px"><span><svg width="8" height="7"><rect width="2" height="6" y="1" fill="#aaa"/><path d="M3 1h4v6H3z" fill="#aaa"/></svg>Like</span><span><svg width="9" height="7"><ellipse cx="4.5" cy="3" rx="4.5" ry="3" fill="#aaa"/></svg>Comment</span><span><svg width="8" height="7"><circle cx="1.5" cy="3.5" r="1.3" fill="#aaa"/><circle cx="6.5" cy="1.3" r="1.3" fill="#aaa"/><circle cx="6.5" cy="5.7" r="1.3" fill="#aaa"/><path d="M1.5 3.5L6.5 1.3M1.5 3.5L6.5 5.7" stroke="#aaa"/></svg>Share</span></div>
</article>
<div class="abs reply" style="top:649px"><div class="me" role="img" aria-label="Your photo"></div><div class="input">Write Comment...<svg width="8" height="7"><rect y="1.5" width="8" height="5.5" rx="1" fill="#999"/><circle cx="4" cy="4.2" r="1.5" fill="#fff"/></svg></div></div>

<!-- post 3 -->
<article class="abs post" style="top:682px;height:215px">
  <div class="head"><div class="pic" role="img" aria-label="Author photo"></div><div><div class="name">White</div><div class="time">10 hrs</div></div></div>
  <div class="photo" style="top:41px;height:145px;background:linear-gradient(#8e9890 0%,#b9bfb4 50%,#e3e1d8 100%)" role="img" aria-label="Businessman in an office chair before a rising financial chart"></div>
  <div class="actions" style="top:197px"><span><svg width="8" height="7"><rect width="2" height="6" y="1" fill="#aaa"/><path d="M3 1h4v6H3z" fill="#aaa"/></svg>Like</span><span><svg width="9" height="7"><ellipse cx="4.5" cy="3" rx="4.5" ry="3" fill="#aaa"/></svg>Comment</span><span><svg width="8" height="7"><circle cx="1.5" cy="3.5" r="1.3" fill="#aaa"/><circle cx="6.5" cy="1.3" r="1.3" fill="#aaa"/><circle cx="6.5" cy="5.7" r="1.3" fill="#aaa"/><path d="M1.5 3.5L6.5 1.3M1.5 3.5L6.5 5.7" stroke="#aaa"/></svg>Share</span></div>
</article>
<div class="abs reply" style="top:902px"><div class="me" role="img" aria-label="Your photo"></div><div class="input">Write Comment...<svg width="8" height="7"><rect y="1.5" width="8" height="5.5" rx="1" fill="#999"/><circle cx="4" cy="4.2" r="1.5" fill="#fff"/></svg></div></div>

<!-- post 4 -->
<article class="abs post" style="top:935px;height:175px">
  <div class="head"><div class="pic" role="img" aria-label="Author photo"></div><div><div class="name">Hallam</div><div class="time">10 hrs</div></div></div>
  <div class="photo" style="top:43px;height:111px;background:linear-gradient(120deg,#1f4f7a 0%,#4f87b8 35%,#9fc3e0 65%,#e8f0f6 100%)" role="img" aria-label="Glass office tower against the sky"></div>
  <div class="actions" style="top:163px"><span><svg width="8" height="7"><rect width="2" height="6" y="1" fill="#aaa"/><path d="M3 1h4v6H3z" fill="#aaa"/></svg>Like</span><span><svg width="9" height="7"><ellipse cx="4.5" cy="3" rx="4.5" ry="3" fill="#aaa"/></svg>Comment</span><span><svg width="8" height="7"><circle cx="1.5" cy="3.5" r="1.3" fill="#aaa"/><circle cx="6.5" cy="1.3" r="1.3" fill="#aaa"/><circle cx="6.5" cy="5.7" r="1.3" fill="#aaa"/><path d="M1.5 3.5L6.5 1.3M1.5 3.5L6.5 5.7" stroke="#aaa"/></svg>Share</span></div>
</article>
<div class="abs reply" style="top:1114px"><div class="me" role="img" aria-label="Your photo"></div><div class="input">Write Comment...<svg width="8" height="7"><rect y="1.5" width="8" height="5.5" rx="1" fill="#999"/><circle cx="4" cy="4.2" r="1.5" fill="#fff"/></svg></div></div>

<!-- right column -->
<section class="abs people">
  <div class="person"><b role="img" aria-label="Contact photo"></b>Ritchie<i></i></div>
  <div class="person"><b role="img" aria-label="Contact photo"></b>Owen T. Barlow<i></i></div>
  <div class="person"><b role="img" aria-label="Contact photo"></b>Felix R. Santos<i></i></div>
  <div class="person"><b role="img" aria-label="Contact photo"></b>Miera<i></i></div>
  <div class="person"><b role="img" aria-label="Contact photo"></b>Irwin<i></i></div>
  <div class="person"><b role="img" aria-label="Contact photo"></b>Bigley<i></i></div>
  <div class="person"><b role="img" aria-label="Contact photo"></b>J. Delorme<i></i></div>
  <div class="person"><b role="img" aria-label="Contact photo"></b>Corin B.<i></i></div>
</section>
<div class="abs people-search"><svg width="8" height="8" viewBox="0 0 8 8"><circle cx="3.3" cy="3.3" r="2.5" fill="none" stroke="#555" stroke-width="1.1"/><path d="M5.2 5.2L7.5 7.5" stroke="#555" stroke-width="1.1"/></svg>Search</div>

<section class="abs events">
  <div class="block-head" style="height:27px">LATEST EVENTS</div>
  <ul>
    <li>Lorem Ipsum is simply dummy text of</li>
    <li>Contrary to popular belief, Lorem Ipsum is</li>
    <li>There are many variations of passages.</li>
    <li>Sed ut perspiciatis unde omnis iste natus error.</li>
    <li>But I must explain to you how all this mistaken.</li>
    <li>There are many variations of passages of Lorem</li>
    <li>Web sites still in their infancy. Various versions</li>
  </ul>
</section>

<section class="abs about">
  <div class="block-head" style="height:27px">ABOUT US</div>
  <div class="body">
    There are many variations of passages of Lorem Ipsum available, but the majority have suffered alteration in some form, by injected humour, or randomised words which don't look even slightly believable. If you are going to use a passage of Lorem Ipsum, you need to be sure there isn't anything.
    <div class="more">READ MORE &gt;&gt;</div>
  </div>
</section>

<footer class="abs footer">Copyrights @ 2015 All Rights Reserved</footer>

</body>
</html>
```